Business Card Design - VNT (company name)

Over 20 years of progressive technology design, migration and management experience that drives business objectives and streamlines operations. Continuously challenge conventions to meet and exceed business security, availability and functionality requirements. Maintain exceptional vendor relationships to ensure ongoing knowledge of emerging products and to secure preferred service agreements. Recruit and utilize top talent and foster a collegial environment that advances innovation and performance excellence. design logo using 3 arrows of different colors green, gold, blue

Industry/Entity Type

Progressive

Contact Information for Business Card

Martin K. Osgood
IT Strategist / Consultant

626.583.2907 MOsgood@vntosgood.example 4817 Brenning Court Pasadena, CA 91104

Colors
0255a3
f37122
fece3e

Requirements
Must have
• Note NEW EMAIL ADDRESS
• MOsgood@vntosgood.example
• NOTE NEW ORDER of the work I do.
• Infrastructure – Systems – Cybersecurity
Nice to have
• main color should be orange

```html
<!DOCTYPE html>
<html lang="en">
<head>
<meta charset="utf-8">
<title>VNT Business Card</title>
<link rel="stylesheet" href="https://fonts.googleapis.com/css2?family=Source+Sans+3:wght@400;600;700&display=swap">
<style>
  :root {
    --orange: #f37122;
    --blue: #0255a3;
    --gold: #fece3e;
    --charcoal: #2d2d2f;
    --ink: #3a3a3a;
    --mist: #d6d6d6;
    --paper: #ffffff;
    --backdrop: #ecebe8;
  }
  html, body {
    margin: 0;
    width: 1200px;
    height: 1200px;
    overflow: hidden;
    background: var(--backdrop);
    font-family: "Source Sans 3", Arial, sans-serif;
  }
  .canvas {
    position: relative;
    width: 1200px;
    height: 1200px;
  }
  .card {
    position: absolute;
    left: 250px;
    width: 700px;
    height: 400px;
    box-shadow: 0 6px 18px rgba(0,0,0,0.18);
    overflow: hidden;
  }
  /* Back face */
  .card-back {
    top: 130px;
    background: var(--charcoal);
  }
  .card-back .brand-name {
    position: absolute;
    top: 95px;
    left: 0;
    width: 100%;
    text-align: center;
    font-size: 120px;
    font-weight: 700;
    letter-spacing: 6px;
    color: var(--mist);
    line-height: 1;
  }
  .card-back .services {
    position: absolute;
    left: 40px;
    right: 40px;
    bottom: 80px;
    font-size: 19px;
    color: var(--mist);
    text-align: center;
    letter-spacing: 0.3px;
  }
  /* Front face */
  .card-front {
    top: 670px;
    background: var(--paper);
  }
  .corner-mark {
    position: absolute;
    top: 32px;
    left: 0;
  }
  .identity {
    position: absolute;
    top: 26px;
    left: 58px;
  }
  .identity .person {
    margin: 0;
    font-size: 30px;
    font-weight: 700;
    color: var(--orange);
    line-height: 1.05;
  }
  .identity .role {
    margin: 0;
    font-size: 18px;
    font-weight: 600;
    color: var(--ink);
  }
  .contact {
    position: absolute;
    top: 160px;
    left: 40px;
    margin: 0;
    padding: 0;
    list-style: none;
    font-size: 17px;
    color: var(--ink);
    line-height: 1.3;
  }
  .contact .gap { margin-top: 6px; }
  .contact .label { color: var(--orange); }
  .front-brand {
    position: absolute;
    top: 175px;
    left: 455px;
    display: flex;
    align-items: center;
    gap: 14px;
  }
  .front-brand .dot {
    width: 22px;
    height: 22px;
    border-radius: 50%;
    background: var(--blue);
  }
  .front-brand .brand-name {
    font-size: 68px;
    font-weight: 700;
    color: var(--orange);
    letter-spacing: 3px;
    line-height: 1;
  }
  .bands {
    position: absolute;
    left: 0;
    bottom: 0;
  }
</style>
</head>
<body>
<main class="canvas">

  <section class="card card-back" aria-label="Card back">
    <div class="brand-name">VNT</div>
    <p class="services">IT Strategist | Consultant &nbsp;Infrastructure | Systems | Cybersecurity</p>
  </section>

  <section class="card card-front" aria-label="Card front">
    <svg class="corner-mark" width="46" height="36" viewBox="0 0 46 36" aria-hidden="true">
      <polygon points="0,0 30,0 0,36" fill="var(--orange)"/>
      <polygon points="30,0 46,0 46,36 0,36" fill="var(--blue)"/>
    </svg>
    <div class="identity">
      <h1 class="person">Martin K. Osgood</h1>
      <p class="role">Managing Director</p>
    </div>

    <ul class="contact">
      <li>4817 Brenning Court</li>
      <li>Pasadena, CA 91104</li>
      <li class="gap"><span class="label">p:</span> 626.583.2907</li>
      <li><span class="label">f:</span> 626.583.2908</li>
      <li><span class="label">e:</span> MOsgood@vntosgood.example</li>
    </ul>

    <div class="front-brand">
      <span class="dot"></span>
      <span class="brand-name">VNT</span>
    </div>

    <svg class="bands" width="700" height="110" viewBox="0 0 700 110" aria-hidden="true">
      <polygon points="0,0 390,0 372,22 0,22" fill="var(--orange)"/>
      <polygon points="405,22 700,22 700,110 0,110 0,84 330,84 372,22" fill="var(--paper)"/>
      <polygon points="380,26 700,26 700,70 340,70" fill="var(--blue)"/>
    </svg>
  </section>

</main>
</body>
</html>
```